Redesign of business card for Cedar Ridge Mechanical

We are looking for a new design for our business cards for Cedar Ridge Mechanical. We are a plumbing & HVAC construction company, operating on the West Coast of Canada and USA. Logo attached.
Industry/Entity Type
Construction - Plumbing & HVAC
Contact Information for Business Card
Name, address, phone numbers, email, website address
Look and feel
Each slider illustrates characteristics of the customer's brand and the style your logo design should communicate.

```html
<!DOCTYPE html>
<html lang="en">
<head>
<meta charset="utf-8">
<title>Cedar Ridge Mechanical – Business Card</title>
<link href="https://fonts.googleapis.com/css2?family=Bebas+Neue&family=Roboto:wght@400&display=swap" rel="stylesheet">
<style>
  :root {
    --backdrop: #b1b1b1;
    --ink: #1b1b1a;
    --paper: #ffffff;
    --text: #2a2a2a;
    --emboss: #5e5e5c;
  }
  * { margin: 0; padding: 0; box-sizing: border-box; }
  html, body { width: 1093px; height: 1200px; overflow: hidden; }
  body { background: var(--backdrop); position: relative; font-family: "Roboto", sans-serif; }

  .card { position: absolute; left: 265px; width: 578px; height: 356px; border-radius: 24px; overflow: hidden; }
  .card--front { top: 226px; background: var(--paper); }
  .card--back { top: 621px; background: var(--ink); }

  .header-band { position: absolute; left: 0; top: 0; width: 100%; height: 109px; background: var(--ink); }
  .company-name { position: absolute; left: 27px; top: 40px; font-family: "Bebas Neue", sans-serif; font-size: 42px; line-height: 1; color: var(--paper); letter-spacing: 0.2px; }

  .brand-lockup { position: absolute; left: 372px; top: 124px; display: flex; align-items: center; gap: 12px; }
  .brand-square { width: 22px; height: 22px; background: var(--ink); }
  .brand-name { font-family: "Bebas Neue", sans-serif; font-size: 30px; line-height: 0.95; color: var(--ink); }

  .accent-bar { position: absolute; left: 0; top: 197px; width: 12px; height: 38px; background: var(--ink); }
  .person-name { position: absolute; left: 27px; top: 194px; font-family: "Bebas Neue", sans-serif; font-size: 33px; line-height: 1; color: var(--text); }
  .person-role { position: absolute; left: 27px; top: 222px; font-size: 16px; color: var(--text); }

  .contact-list { position: absolute; left: 27px; top: 266px; list-style: none; }
  .contact-list li { display: flex; align-items: center; height: 21px; font-size: 16.5px; color: var(--text); }
  .contact-list svg { width: 16px; height: 16px; margin-right: 6px; fill: var(--text); }

  .address { position: absolute; right: 23px; top: 287px; text-align: right; font-size: 16.5px; line-height: 21px; color: var(--text); font-style: normal; }

  .back-lockup { position: absolute; left: 0; top: 0; width: 100%; height: 100%; display: flex; align-items: center; justify-content: center; gap: 16px; }
  .back-square { width: 34px; height: 34px; background: var(--emboss); }
  .back-name { font-family: "Bebas Neue", sans-serif; font-size: 50px; line-height: 1; color: var(--emboss); letter-spacing: 1px; }
</style>
</head>
<body>
  <section class="card card--front">
    <div class="header-band"></div>
    <h1 class="company-name">CEDAR RIDGE MECHANICAL</h1>

    <div class="brand-lockup">
      <span class="brand-square"></span>
      <span class="brand-name">CEDAR RIDGE<br>MECHANICAL</span>
    </div>

    <div class="accent-bar"></div>
    <h2 class="person-name">DANIEL MORROW</h2>
    <p class="person-role">Managing Director</p>

    <ul class="contact-list">
      <li>
        <svg viewBox="0 0 24 24"><path d="M6.6 10.8a15.1 15.1 0 0 0 6.6 6.6l2.2-2.2c.3-.3.7-.4 1-.2 1.1.4 2.3.6 3.6.6.6 0 1 .4 1 1V20c0 .6-.4 1-1 1A17 17 0 0 1 3 4c0-.6.4-1 1-1h3.5c.6 0 1 .4 1 1 0 1.3.2 2.5.6 3.6.1.3 0 .7-.2 1z"/></svg>
        044-321 654 987
      </li>
      <li>
        <svg viewBox="0 0 24 24"><path d="M2 5h20v14H2z M2 5l10 8 10-8" fill="none" stroke="#2a2a2a" stroke-width="0"/><path d="M2 6.5l10 7 10-7V19H2z"/><path d="M2 5h20l-10 7z"/></svg>
        hello@cedarridgemech.com
      </li>
      <li>
        <svg viewBox="0 0 24 24"><circle cx="12" cy="12" r="9.5" fill="none" stroke="#2a2a2a" stroke-width="2"/><path d="M2.5 12h19M12 2.5v19" stroke="#2a2a2a" stroke-width="1.6"/><ellipse cx="12" cy="12" rx="4.5" ry="9.5" fill="none" stroke="#2a2a2a" stroke-width="1.6"/></svg>
        www.cedarridgemech.com
      </li>
    </ul>

    <address class="address">218, Harbour Line Road<br>V5K 0A1, Canada</address>
  </section>

  <section class="card card--back">
    <div class="back-lockup">
      <span class="back-square"></span>
      <span class="back-name">CEDAR RIDGE MECHANICAL</span>
    </div>
  </section>
</body>
</html>
```